The most modern business card ever !!!

Our company call “Vendalo”. Vendalo is a technology company specialized in cruises solutions. Out main product is a platform to reserve cruises. This is a revolutionary platform that make easier to travel agencies and final users to reserve cruises across dozen companies like tibba, wernu, hpv, dgb, etc..We are a “start up”, with a young team of developers and we want to transmit it.. For it, we want something different, a modern business card that represent cruises and technology.. When someone receive this card, this person should say: wowww this is different… this is modern… this is a cruise related company..
- diferent, modern
- traditions business card

```html
<!DOCTYPE html>
<html lang="en">
<head>
<meta charset="utf-8">
<title>Vendalo – Business Card</title>
<link href="https://fonts.googleapis.com/css2?family=Exo+2:wght@600&family=Roboto:wght@400&display=swap" rel="stylesheet">
<style>
  :root {
    --page-bg: #ffffff;
    --card-bg: #1d1d1e;
    --watermark: #232425;
    --mark-tone: #1f2223;
    --brand-light: #d9d9d9;
    --accent: #1ea3dc;
    --accent-soft: rgba(30, 163, 220, 0.75);
    --text: #ffffff;
    --shadow: rgba(0, 0, 0, 0.35);
  }
  * { margin: 0; padding: 0; box-sizing: border-box; }
  html, body { width: 1200px; height: 1200px; overflow: hidden; background: var(--page-bg); }
  .canvas { position: relative; width: 1200px; height: 1200px; }
  .card {
    position: absolute; top: 198px; width: 520px; height: 802px;
    background: var(--card-bg);
    box-shadow: 6px 8px 14px var(--shadow);
    overflow: hidden;
  }
  .card--front { left: 72px; }
  .card--back { left: 614px; }
  .watermark {
    position: absolute; top: 22px; left: 0; width: 100%;
    text-align: center;
    font-family: "Exo 2", sans-serif; font-weight: 600;
    font-size: 104px; letter-spacing: 4px;
    color: var(--watermark);
  }
  .brand-mark-area {
    position: absolute; left: 120px; top: 212px; width: 290px; height: 384px;
    background: radial-gradient(ellipse at center, var(--mark-tone) 0%, rgba(31,34,35,0.6) 45%, rgba(29,29,30,0) 72%);
  }
  .brand-name {
    position: absolute; top: 652px; left: 0; width: 100%;
    text-align: center;
    font-family: "Exo 2", sans-serif; font-weight: 600;
    font-size: 104px; letter-spacing: 4px;
    color: var(--brand-light);
  }
  .person { position: absolute; top: 240px; left: 0; width: 100%; text-align: center; }
  .person__name {
    font-family: "Exo 2", sans-serif; font-weight: 600;
    font-size: 48px; letter-spacing: 1px; line-height: 1.1;
    color: var(--accent);
  }
  .person__role {
    font-family: Roboto, sans-serif; font-size: 20px;
    color: var(--text); margin-top: 2px;
  }
  .divider {
    display: block; height: 4px;
    background: var(--accent-soft);
  }
  .divider--title { width: 166px; margin: 10px auto 0; }
  .divider--side { width: 134px; }
  .contact-icons {
    position: absolute; top: 498px; left: 0; width: 100%;
    display: flex; justify-content: center; gap: 13px;
  }
  .contact-icons svg { width: 27px; height: 27px; }
  .contact-list {
    position: absolute; top: 546px; left: 0; width: 100%;
    list-style: none; text-align: center;
    font-family: Roboto, sans-serif; font-size: 21px; line-height: 30px;
    color: var(--text); letter-spacing: 0.5px;
  }
  .address-row {
    position: absolute; top: 704px; left: 0; width: 100%;
    display: flex; align-items: center; justify-content: space-between;
  }
  .address {
    font-family: Roboto, sans-serif; font-size: 20px; line-height: 24px;
    color: var(--text); text-align: center; font-style: normal; letter-spacing: 0.5px;
  }
</style>
</head>
<body>
<main class="canvas">
  <section class="card card--front">
    <div class="watermark">Vendalo</div>
    <div class="brand-mark-area" role="img" aria-label="Faint large brand mark decoration"></div>
    <div class="brand-name">Vendalo</div>
  </section>

  <section class="card card--back">
    <div class="watermark">Vendalo</div>

    <div class="person">
      <h1 class="person__name">Dara Quinlan</h1>
      <p class="person__role">Founder &amp; CEO</p>
      <span class="divider divider--title" role="img" aria-label="Blue chevron pattern divider"></span>
    </div>

    <div class="contact-icons">
      <svg viewBox="0 0 26 26" aria-label="Phone"><circle cx="13" cy="13" r="13" fill="var(--accent)"/><path d="M8.5 7.5l2.5-.5 1.2 3-1.5 1.2a8 8 0 0 0 3.6 3.6l1.2-1.5 3 1.2-.5 2.5c-5 .5-10-4.5-9.5-9.5z" fill="#fff"/></svg>
      <svg viewBox="0 0 26 26" aria-label="Email"><circle cx="13" cy="13" r="13" fill="var(--accent)"/><rect x="7" y="9" width="12" height="9" rx="1.5" fill="#fff"/><polyline points="7.5,9.8 13,14 18.5,9.8" fill="none" stroke="var(--accent)" stroke-width="1.3"/></svg>
      <svg viewBox="0 0 26 26" aria-label="Website"><circle cx="13" cy="13" r="13" fill="var(--accent)"/><g fill="none" stroke="#fff" stroke-width="1.1"><circle cx="13" cy="13" r="6.5"/><ellipse cx="13" cy="13" rx="2.8" ry="6.5"/><line x1="6.5" y1="13" x2="19.5" y2="13"/><line x1="7.5" y1="9.8" x2="18.5" y2="9.8"/><line x1="7.5" y1="16.2" x2="18.5" y2="16.2"/></g></svg>
    </div>

    <ul class="contact-list">
      <li>000 000 0000</li>
      <li>d.quinlan@vendalo.com</li>
      <li>www.vendalo.com</li>
    </ul>

    <div class="address-row">
      <span class="divider divider--side" role="img" aria-label="Blue chevron pattern divider"></span>
      <address class="address">48 Harbour Lane, Suite# B<br>Bristol, UK 400B17</address>
      <span class="divider divider--side" role="img" aria-label="Blue chevron pattern divider"></span>
    </div>
  </section>
</main>
</body>
</html>
```